E-Commerce Web Design Project - Online Designer Childrens Clothing

I currently have a website at http://qrk.example/Tm4vRa but I am not happy with the look and feel. I mainly want black and white colours as my images will have splashes of colour

I am going for a complete new look and will require the following:

1. Home page - to have categories listed on the left side bar and large scrolling images in the center (600px by 450px) with 3 static boxes equally spaced underneath (325px by 142px) so that I can change them to different links. 3 static boxes to be on the right side bar in vertical position each size (198px by 145px).

2. category pages - to have image across the width of the page for my category title page eg. Marbury's kids. category pages to have 3 products across and ability to view all or go down to the page fold.

3. product Details pages - product image to be on the left side bar. All drop down boxes to be of equal size in width and length. Other products you may like is to be removed. Please see the following links as to what I would like it to look like layout wise http://qrk.example/Wp7dGs

4. All other pages such as the Contact us, T's and C's, About Us, Ordering and Delivery etc to have the same template where I will be able to keep adding pages as I need to.

I will be transferring my services to Tillvane and will seek a web developer once the design is confirmed.

3 websites that i love are the following:
http://qrk.example/Wp7dGs
http://qrk.example/Bz2fUe
http://qrk.example/3JtYon
http://qrk.example/gumaLQ

I want my website to be sleek and modern and have a fashion magazine feel to it. the layout is to be clean with everything in proportion. I already have my logo in greyscale that I have attached it to this project.

Please let me know if you have further questions.
Updates

would love to see more designs!i have added a couple more logo files also to add.

Reason: I have now guaranteed tthis project so hopefully more designs will come through!!

I have now guranteed this project so would love to see a few more designs!!!

Reason: I need time to review all submissions and request changes if need be

Target Market(s)

women 25-45 on good disposable income who like their designer brands and love to dress their boys in them

Industry/Entity Type

Fashion

Requirements
Must have
• must be easy to navigate and not to busy. nice and sleek with a fashion magazine feel to it. want it to be more monotone in black and white as my images will add colour
Nice to have
• I love the look of the following websites.

Home Pages:
http://qrk.example/3JtYon
http://qrk.example/Bz2fUe
http://qrk.example/hRN8T4
http://qrk.example/wiDk2v
http://qrk.example/Ezm5o
http://qrk.example/xTcHoa
http://qrk.example/P3sRyd

Category Page:

Product Details Page:
http://qrk.example/Wp7dGs
http://qrk.example/NuqaWt
http://qrk.example/RfzvIm

Products details page:
http://qrk.example/G6WJ9k
http://qrk.example/Wp7dGs

Should not have
• I do not want any quirky or childlike illustrations or the colorful blue. this website is for boys clothing but it targeted at women!!

```html
<!DOCTYPE html>
<html lang="en">
<head>
<meta charset="utf-8">
<title>Brightlane Kids Clothing</title>
<link href="https://fonts.googleapis.com/css2?family=Source+Sans+3:wght@400;600&family=PT+Sans+Narrow&display=swap" rel="stylesheet">
<style>
:root{
  --band:#58585a;
  --ink:#111;
  --text:#444;
  --muted:#666;
  --line:#ddd;
  --card:#5f5f61;
  --card-dark:#4a4a4c;
  --gold:#f2b705;
  --sale:#e8531d;
  --blue:#1f5fa8;
  --green:#7aa84a;
  --white:#fff;
}
*{box-sizing:border-box;margin:0;padding:0}
html,body{width:1069px;height:1200px;overflow:hidden;background:var(--white)}
body{position:relative;font-family:"Source Sans 3",Arial,sans-serif;color:var(--text)}
.abs{position:absolute}
.topbar{left:0;top:0;width:1069px;height:19px;background:var(--band)}
.bag{left:757px;top:0;width:165px;height:36px;background:var(--ink);color:var(--white);font-size:11.5px;font-weight:600;display:flex;align-items:center}
.bag span{flex:1;text-align:center}
.bag span+span{border-left:1px solid #444}
.logo{left:144px;top:46px;display:flex;align-items:center;gap:8px;color:#555;font-size:21px;letter-spacing:3px;line-height:1.05}
.logo i{width:14px;height:14px;background:#555;display:block}
.search{left:708px;top:61px;width:214px;height:28px;border:1px solid var(--line);border-radius:3px;font-size:11px;color:var(--muted);padding:7px 10px}
.search svg{position:absolute;right:8px;top:6px}
.nav{left:146px;top:112px;width:776px;height:24px;background:linear-gradient(#666,#3f3f41);border-radius:3px;display:flex}
.nav a{flex:1;color:var(--white);text-decoration:none;font-size:11px;text-align:center;line-height:24px;border-left:1px solid #777}
.nav a:first-child{border-left:0}
.shop-head{left:145px;top:149px;width:260px;height:25px;background:linear-gradient(#4c4c4e,#111);border-radius:3px;color:var(--white);font-size:13px;padding:4px 12px}
.cats{left:155px;top:186px;width:247px;list-style:none}
.cats li{height:28px;border-bottom:1px solid #e6e6e6;font-size:10.5px;color:#555;line-height:28px;padding-left:12px;position:relative}
.cats li::before{content:"";position:absolute;left:2px;top:12px;border:2.5px solid transparent;border-left:3px solid #555}
.cats li:last-child{border-bottom:0}
.hero{left:426px;top:147px;width:496px;height:374px;background:linear-gradient(120deg,#8c4a3a 0%,#b89a92 40%,#d9c2c0 60%,#6b5b55 100%);box-shadow:0 1px 4px rgba(0,0,0,.4)}
.promo{top:535px;width:256px;height:118px;background:var(--card);border-radius:3px;color:var(--white)}
.promo::after{content:"";position:absolute;left:0;right:0;top:32px;bottom:0;background:linear-gradient(var(--card-dark),#6a6a6c);z-index:0;border-radius:0 0 3px 3px}
.promo *{position:relative;z-index:1}
.promo h3{font-weight:400;font-size:13px;padding:9px 0 0 14px;height:32px}
.promo .name{position:absolute;left:27px;top:46px;font-size:12px}
.promo .price{position:absolute;left:27px;top:64px;font-size:12.5px;color:var(--gold)}
.btn{position:absolute;font-size:10px;color:var(--white);background:#222;border-radius:3px;padding:1px 10px;line-height:16px}
.promo .btn{left:26px;top:89px}
.promo .shot{position:absolute;right:18px;top:12px;width:72px;height:100px;border-radius:6px}
.welcome{left:147px;top:670px;width:589px;height:372px;border:1px solid var(--line);border-radius:4px}
.welcome h2{margin:8px 7px 0;height:24px;background:linear-gradient(#3d3d3f,#1b1b1c);color:var(--white);font-family:"PT Sans Narrow",sans-serif;font-weight:400;font-size:14px;padding:3px 10px;border-radius:3px}
.welcome h4{font-family:"PT Sans Narrow",sans-serif;font-weight:400;font-size:14px;color:#222;margin:15px 11px 12px}
.welcome p{font-size:10.2px;line-height:18.2px;color:#555;margin:0 11px 16px;text-align:justify}
.side{left:757px;width:165px;height:120px;border:1px solid var(--line);border-radius:4px;background:linear-gradient(#fff,#f0f0f0)}
.side h3{position:absolute;left:12px;top:8px;font-weight:400;font-size:19px;z-index:2}
.side .d{position:absolute;left:12px;top:40px;font-size:10px;line-height:15px;color:#555;width:70px;z-index:2}
.side .p{position:absolute;left:12px;top:70px;font-size:14px;color:var(--sale);z-index:2;white-space:nowrap}
.side .btn{left:12px;top:95px;padding:0 3px;font-size:9.5px;line-height:14px;z-index:2}
.side .shot{position:absolute;right:12px;top:9px;width:60px;height:104px;border-radius:6px;z-index:1}
.footer{left:0;top:1060px;width:1069px;height:140px;background:var(--band);color:var(--white);text-align:center;font-size:10.5px}
.follow{position:absolute;left:0;right:0;top:25px;display:flex;justify-content:center;align-items:center;gap:10px}
.follow i{width:20px;height:20px;border-radius:50%;background:radial-gradient(circle at 40% 35%,#7fb3e6,#1f5fa8);border:1px solid #ccc;display:block}
.links{position:absolute;left:0;right:0;top:72px}
.copy{position:absolute;left:0;right:0;top:94px}
.ver{position:absolute;right:26px;top:107px;font-size:10px}
</style>
</head>
<body>
<div class="abs topbar"></div>
<div class="abs bag"><span>View Bag</span><span>Total: AU$0.00</span></div>

<div class="abs logo"><i></i><span>BRIGHTLANE KIDS<br>CLOTHING</span></div>

<div class="abs search">Search
  <svg width="14" height="14" viewBox="0 0 14 14"><circle cx="5.5" cy="5.5" r="4" fill="none" stroke="#555" stroke-width="1.6"/><line x1="8.5" y1="8.5" x2="13" y2="13" stroke="#555" stroke-width="2"/></svg>
</div>

<nav class="abs nav">
  <a>Home</a><a>About Us</a><a>Blog</a><a>Sizing</a><a>Media</a><a>Contact Us</a><a>Login</a>
</nav>

<div class="abs shop-head">SHOP</div>
<ul class="abs cats">
  <li>T Shirts And Tops</li><li>Shirts And Jumpers</li><li>Pants And Shorts</li><li>Jeans</li>
  <li>Jackets and Coats</li><li>Beachwear</li><li>Sleepwear</li><li>Shoes and Socks</li>
  <li>Accessories</li><li>Bags &amp; Luggages</li><li>Gift Certificates</li>
</ul>

<div class="abs hero" role="img" aria-label="Feature photo: a boy in a checked short-sleeve shirt sitting by a brick wall"></div>

<div class="abs promo" style="left:147px">
  <h3>T Shirts And Tops</h3>
  <div class="name">Marbury's Kids LS Tee</div>
  <div class="price">AU$47.95</div>
  <span class="btn">more details</span>
  <div class="shot" role="img" aria-label="Grey long-sleeve printed tee" style="background:linear-gradient(#d8d8d8,#b8b8b8)"></div>
</div>
<div class="abs promo" style="left:406px">
  <h3>Shirts And Jumpers</h3>
  <div class="name">Marbury's Kids LS Shirt</div>
  <div class="price">AU$47.95</div>
  <span class="btn">more details</span>
  <div class="shot" role="img" aria-label="White long-sleeve button shirt" style="background:linear-gradient(#fafafa,#dcdcdc)"></div>
</div>
<div class="abs promo" style="left:665px">
  <h3>Pants And Shorts</h3>
  <div class="name">Marbury's Kids LS Tee</div>
  <div class="price">AU$47.95</div>
  <span class="btn">more details</span>
  <div class="shot" role="img" aria-label="Orange checked shorts" style="background:linear-gradient(#e8b890,#c98a5c);height:80px;top:24px"></div>
</div>

<section class="abs welcome">
  <h2>Welcome to Our Site</h2>
  <h4>Designer Style for MiniMen</h4>
  <p>So your little boy is turning into a little man and you're finding it extremely difficult to find fashionable clothes to help him develop his own sense of style. You are not alone! With the multitude of kid's clothing stores all catering mainly to little girls, parents of boys in their "tween-age" years (8 to 14 years old) obviously have their work cut out for them. Having done considerable research, I discovered that clothes in children's wear departments were either to small or clothes in men's stores were to big!!</p>
  <p>Brightlane Kids Clothing is here to change all of that!! We offer a stylish collection of designer clothes specifically targeted for this age group.</p>
  <p>Brightlane Kids Clothing was created for the sole purpose of providing boys with the latest fashions. We believe young men deserve to have as much choice as girls! We stock well known Australian and International Brands such as Hollowpine, Varenne, Marbury's Kids, Quillex, Rampart Denim, Ludo &amp; Fenn and many more! There are heaps of styles to choose from such as T-Shirts and Jeans to cool Shoes and funky PJ's!</p>
  <p>Please enjoy shopping at Brightlane Kids Clothing and do not hesitate to contact us at info@brightlanekids.example should you require further assistance.</p>
</section>

<div class="abs side" style="top:670px">
  <h3 style="color:var(--blue)">Jeans</h3>
  <div class="d">Rampart Denim Skinny Jeans</div>
  <div class="p">AU$59.95</div>
  <span class="btn" style="background:var(--blue)">more details</span>
  <div class="shot" role="img" aria-label="Blue skinny jeans" style="background:linear-gradient(#3a78d0,#1b4f9c);width:56px"></div>
</div>
<div class="abs side" style="top:797px">
  <h3 style="color:var(--green)">Beachwear</h3>
  <div class="d">Hollowpine Bucket Hat</div>
  <div class="p">SALE AU$17.00</div>
  <span class="btn" style="background:var(--green)">more details</span>
  <div class="shot" role="img" aria-label="Green floral board shorts" style="background:linear-gradient(#a6d07a,#5f9a3c);width:58px;right:8px;top:50px;height:64px"></div>
</div>
<div class="abs side" style="top:923px">
  <h3 style="color:#222">Sleepwear</h3>
  <div class="d" style="top:55px;width:90px">Ludo &amp; Fenn PJ Set</div>
  <div class="p" style="top:78px">AU$49.95</div>
  <span class="btn" style="background:#222;top:101px">more details</span>
  <div class="shot" role="img" aria-label="Navy long-sleeve top with striped pyjama pants" style="background:linear-gradient(#1d2550 0%,#1d2550 45%,#c8ccd8 55%,#9ea4b6 100%);width:50px;right:4px;top:22px;height:94px"></div>
</div>

<footer class="abs footer">
  <div class="follow">Follow Us <i></i><i></i></div>
  <div class="links">sign up | privacy &amp; security | orders &amp; delivery | terms of use | payment options | links | testimonials | site map</div>
  <div class="copy">Copyrights @ 2012 All Rights Reserved</div>
  <div class="ver">X37</div>
</footer>
</body>
</html>
```